Fenwick Grading LTD - website for irrigation & Landscape Lighting & Buried service wire

Looking for a website to help promote my business with Irrigation (installation, service, etc) and buried service wire/drainage solutions.

Commercial/Residential

Landscape lighting.

I’ll get photos in the trucks and trailers to upload as well maybe the machine as well.

Target Market(s)

Homeowners who want green grass and beautiful gardens. Beautiful landscape lighting

Industry/Entity Type

Irrigation systems and landscape lighting and buried service wire to homes and offering Drainage soltions.

Coding

Coded - Design and coding required

Number of Pages Required

4 page

Colors
F0912C
F2A743
F7CA91
FBE8D2
FDF5EE

Requirements
Must have
• was hoping to link up my email on fenwickgrading@mailbox-example.net with the website if possible.
Nice to have
• Page for Irrigation, page for landscape lighting, page buried service wire & drainage soltions.

```html
<!DOCTYPE html>
<html lang="en">
<head>
<meta charset="utf-8">
<title>Fenwick Grading LTD</title>
<link rel="stylesheet" href="https://fonts.googleapis.com/css2?family=Montserrat:wght@400;500;600;700;800&family=Roboto:wght@400&display=swap">
<style>
:root{
  --orange:#F0912C;
  --orange-2:#F2A743;
  --orange-3:#F7CA91;
  --cream:#FBE8D2;
  --cream-2:#FDF5EE;
  --ink:#111111;
  --text:#444444;
  --grey-band:#ebebeb;
  --footer:#000000;
  --white:#ffffff;
}
*{box-sizing:border-box;margin:0;padding:0}
html,body{width:1200px;height:3687px;overflow:hidden}
body{font-family:"Montserrat",sans-serif;color:var(--text);background:var(--white);position:relative}
.abs{position:absolute}

/* header */
.site-header{position:absolute;left:0;top:0;width:1200px;height:148px;background:var(--white)}
.topbar{position:absolute;left:380px;top:0;width:820px;height:62px;background:var(--orange);clip-path:polygon(0 0,100% 0,100% 100%,56px 100%)}
.topbar-item{position:absolute;top:19px;color:var(--white);font-size:13px;font-weight:600;display:flex;align-items:center;gap:12px}
.brand{position:absolute;left:110px;top:38px;width:190px;text-align:center;color:var(--orange);font-weight:700;font-size:24px;line-height:30px;letter-spacing:1px}
.brand-sub{font-size:17px;letter-spacing:2px;line-height:22px}
.main-nav{position:absolute;left:446px;top:96px;width:644px;display:flex;gap:33px;font-size:13.5px;color:#333;border-bottom:1px solid #ddd;height:32px}
.main-nav a{color:inherit;text-decoration:none;position:relative}
.main-nav a.active::after{content:"";position:absolute;left:0;right:-8px;bottom:-2px;height:2px;background:var(--orange)}

/* hero */
.hero{position:absolute;left:0;top:148px;width:1200px;height:602px;background:linear-gradient(120deg,#4f6a26 0%,#6f8a34 35%,#587a2a 60%,#3d5420 100%)}
.hero-copy{position:absolute;left:103px;top:70px;color:var(--white)}
.hero-welcome{font-size:26px;font-weight:600}
.hero-title{font-size:52px;font-weight:800;margin-top:12px;line-height:1}
.hero-lead{font-size:17px;font-weight:600;margin:20px 0 0 5px}
.hero-ticks{list-style:none;margin-top:4px}
.hero-ticks li{display:flex;align-items:center;gap:12px;font-size:17px;font-weight:600;height:38px;margin-left:12px}
.btn{display:inline-block;font-family:"Montserrat",sans-serif;font-weight:600;font-size:14px;text-align:center}
.btn-white{background:var(--white);color:var(--ink)}
.btn-orange{background:var(--orange);color:var(--white)}

/* about */
.photo{position:absolute;border-radius:14px}
.section-title{font-weight:700;font-size:36px;color:var(--ink)}
.section-title span{color:var(--orange)}
.about-text{position:absolute;left:649px;top:902px;width:444px;font-size:13.5px;line-height:25px;text-align:justify;color:#444}
.about-text p{margin-bottom:14px}

/* services */
.services-band{position:absolute;left:0;top:1356px;width:1200px;height:345px;background:var(--grey-band)}
.service-card{position:absolute;top:1532px;width:319px;height:411px;background:var(--white);box-shadow:0 2px 6px rgba(0,0,0,.18)}
.service-img{position:absolute;left:0;top:0;width:100%;height:228px;border-bottom:4px solid var(--orange);clip-path:polygon(0 0,100% 0,100% 100%,0 88%)}
.service-icon{position:absolute;top:168px;width:66px;height:66px;border-radius:50%;background:var(--white);border:3px solid var(--orange);display:flex;align-items:center;justify-content:center}
.service-title{position:absolute;top:244px;width:100%;text-align:center;font-weight:600;font-size:17px;color:var(--ink)}
.service-text{position:absolute;top:274px;left:22px;right:22px;text-align:center;font-size:13px;line-height:23px;color:#444}
.carousel-arrow{position:absolute;top:1758px}

/* contact */
.contact{position:absolute;left:0;top:2778px;width:1200px;height:512px;background:linear-gradient(135deg,#ef8f2c 0%,#f2a743 45%,#ee8d2a 100%)}
.field{position:absolute;background:var(--white);border-radius:5px;font-size:12.5px;color:#666;display:flex;align-items:center;gap:10px;padding-left:14px}

/* footer */
.site-footer{position:absolute;left:0;top:3290px;width:1200px;height:397px;background:var(--footer);color:var(--white)}
.footer-nav{position:absolute;top:237px;left:0;width:1200px;display:flex;justify-content:center;gap:36px;font-size:15px}
.social{position:absolute;top:283px;left:545px;display:flex;gap:8px}
.social span{width:22px;height:22px;background:var(--white);border-radius:2px}
.footer-rule{position:absolute;left:108px;top:347px;width:976px;height:1px;background:#666}
.copyright{position:absolute;top:367px;width:1200px;text-align:center;font-family:"Roboto",sans-serif;font-size:12px}
</style>
</head>
<body>

<header class="site-header">
  <div class="brand">FENWICK<br><span class="brand-sub">GRADING LTD</span></div>
  <div class="topbar">
    <div class="topbar-item" style="left:76px">
      <svg width="14" height="18" viewBox="0 0 14 18"><path d="M7 0a7 7 0 0 0-7 7c0 5 7 11 7 11s7-6 7-11a7 7 0 0 0-7-7zm0 10a3 3 0 1 1 0-6 3 3 0 0 1 0 6z" fill="#fff"/></svg>
      Lorem Ipsum,USA - 437916</div>
    <div class="topbar-item" style="left:344px">
      <svg width="16" height="16" viewBox="0 0 24 24"><path d="M6.6 10.8a15 15 0 0 0 6.6 6.6l2.2-2.2a1 1 0 0 1 1-.25 11 11 0 0 0 3.6.6 1 1 0 0 1 1 1V20a1 1 0 0 1-1 1A17 17 0 0 1 3 4a1 1 0 0 1 1-1h3.5a1 1 0 0 1 1 1 11 11 0 0 0 .6 3.6 1 1 0 0 1-.25 1z" fill="#fff"/></svg>
      +1 888 888 8888</div>
    <div class="topbar-item" style="left:564px;font-size:12px">
      <svg width="18" height="13" viewBox="0 0 18 13"><rect width="18" height="13" rx="1.5" fill="#fff"/><path d="M1 1l8 6 8-6" stroke="#F0912C" stroke-width="1.6" fill="none"/></svg>
      fenwickgrading@mailbox-example.net</div>
  </div>
  <nav class="main-nav">
    <a class="active">Home</a><a>Irrigation installs</a><a>Service</a><a>Landscape Lighting</a><a>Fiber Optic Installation</a>
  </nav>
</header>

<section class="hero" role="img" aria-label="Hands fitting a garden hose onto an orange lawn sprinkler in tall green grass">
  <div class="hero-copy">
    <div class="hero-welcome">Welcome To</div>
    <h1 class="hero-title">Fenwick Grading.</h1>
    <p class="hero-lead">Home owners who want</p>
    <ul class="hero-ticks">
      <li><svg width="28" height="26" viewBox="0 0 28 26"><path d="M2 14l8 9L26 2" stroke="#F0912C" stroke-width="4" fill="none" stroke-linecap="round"/></svg>green grass and</li>
      <li><svg width="28" height="26" viewBox="0 0 28 26"><path d="M2 14l8 9L26 2" stroke="#F0912C" stroke-width="4" fill="none" stroke-linecap="round"/></svg>beautiful gardens</li>
      <li><svg width="28" height="26" viewBox="0 0 28 26"><path d="M2 14l8 9L26 2" stroke="#F0912C" stroke-width="4" fill="none" stroke-linecap="round"/></svg>&nbsp;Beautiful landscape lighting</li>
    </ul>
  </div>
  <div class="btn btn-white abs" style="left:110px;top:342px;width:131px;height:43px;line-height:43px">Get Started</div>
</section>

<section class="about">
  <div class="photo" style="left:106px;top:842px;width:230px;height:230px;background:linear-gradient(160deg,#6b7d93,#c9c1b8 60%,#e29a6a)" role="img" aria-label="Technician in a hard hat splicing fibre cables on a rooftop"></div>
  <div class="photo" style="left:108px;top:1090px;width:222px;height:155px;background:linear-gradient(180deg,#8fb9e0,#4d8a3a 55%,#c8c4b8)" role="img" aria-label="Landscaped park path with trees and shrubs"></div>
  <div class="photo" style="left:356px;top:862px;width:222px;height:155px;background:linear-gradient(150deg,#8a9b6a,#3aa0c0 50%,#6a4e3a)" role="img" aria-label="Gardener installing irrigation tubing among plants"></div>
  <div class="photo" style="left:354px;top:1034px;width:230px;height:229px;background:linear-gradient(180deg,#e8b48a,#5a4a3e 50%,#4f8a34)" role="img" aria-label="Craftsman house with lit windows and a landscaped front lawn at dusk"></div>
  <h2 class="section-title abs" style="left:645px;top:848px">About <span>Us</span></h2>
  <div class="about-text">
    <p>Lorem ipsum dolor sit amet, consectetur adipiscing elit, sed do eiusmod tempor incididunt ut labore et dolore magna aliqua. Ut enim ad minim veniam, quis nostrud exercitation ullamco laboris nisi ut aliquip ex ea commodo consequat.</p>
    <p>Duis aute irure dolor in reprehenderit in voluptate velit esse cillum dolore eu fugiat nulla pariatur. Excepteur sint occaecat cupidatat non proident, sunt in culpa qui officia deserunt mollit anim id est laborum.</p>
    <p>Excepteur sint occaecat cupidatat non proident, sunt in culpa qui officia deserunt mollit anim id est laborum.</p>
  </div>
  <div class="btn btn-orange abs" style="left:647px;top:1202px;width:131px;height:43px;line-height:43px">Get Started</div>
</section>

<section class="services">
  <div class="services-band"></div>
  <h2 class="section-title abs" style="left:0;width:1200px;text-align:center;top:1406px">Our <span>Services</span></h2>
  <p class="abs" style="left:0;width:1200px;text-align:center;top:1466px;font-size:14px;font-weight:500;color:#222">Irrigation systems and landscape lighting and fiber optic installation to homes</p>

  <svg class="carousel-arrow" style="left:26px" width="26" height="20" viewBox="0 0 26 20"><path d="M24 10H3M10 2L2 10l8 8" stroke="#999" stroke-width="2.4" fill="none"/></svg>
  <svg class="carousel-arrow" style="left:1148px" width="26" height="20" viewBox="0 0 26 20"><path d="M2 10h21M16 2l8 8-8 8" stroke="#999" stroke-width="2.4" fill="none"/></svg>

  <article class="service-card" style="left:108px">
    <div class="service-img" style="background:linear-gradient(180deg,#e6a27a,#4a3a30 55%,#4c8a30)" role="img" aria-label="Large home with landscape lighting and green lawn"></div>
    <div class="service-icon" style="left:20px"><svg width="30" height="30" viewBox="0 0 30 30"><circle cx="15" cy="11" r="7" fill="none" stroke="#111" stroke-width="2.5"/><rect x="11" y="19" width="8" height="6" fill="#111"/><path d="M15 1v2M4 11H2M28 11h-2" stroke="#111" stroke-width="2"/></svg></div>
    <h3 class="service-title">Landscape Lighting</h3>
    <p class="service-text">Lorem ipsum dolor sit amet, consectetur adipiscing elit, sed do eiusmod tempor incididunt ut labore et dolore magna aliqua.</p>
  </article>
  <article class="service-card" style="left:441px">
    <div class="service-img" style="background:linear-gradient(135deg,#2a2a2e,#6a3a20 50%,#c05a28)" role="img" aria-label="Technician working at an illuminated fibre optic panel"></div>
    <div class="service-icon" style="left:20px"><svg width="26" height="32" viewBox="0 0 26 32"><rect x="6" y="10" width="14" height="20" rx="2" fill="#111"/><rect x="10" y="3" width="2.5" height="8" fill="#111"/><rect x="14" y="3" width="2.5" height="8" fill="#111"/></svg></div>
    <h3 class="service-title" style="top:240px">Fiber Optic Installation</h3>
    <p class="service-text">Lorem ipsum dolor sit amet, consectetur adipiscing elit, sed do eiusmod tempor incididunt ut labore et dolore magna aliqua.</p>
  </article>
  <article class="service-card" style="left:772px">
    <div class="service-img" style="background:linear-gradient(120deg,#5a7a2a,#8aa848 50%,#3e6a2a)" role="img" aria-label="Hands attaching a hose to a lawn sprinkler"></div>
    <div class="service-icon" style="left:12px"><svg width="32" height="22" viewBox="0 0 32 22"><rect x="8" y="6" width="16" height="8" fill="#111"/><rect x="2" y="3" width="5" height="14" fill="#111"/><rect x="25" y="3" width="5" height="14" fill="#111"/><circle cx="11" cy="19" r="2" fill="#111"/><circle cx="21" cy="19" r="2" fill="#111"/></svg></div>
    <h3 class="service-title">Irrigation Installs</h3>
    <p class="service-text">Lorem ipsum dolor sit amet, consectetur adipiscing elit, sed do eiusmod tempor incididunt ut labore et dolore magna aliqua.</p>
  </article>
</section>

<section class="gallery">
  <h2 class="section-title abs" style="left:0;width:1200px;text-align:center;top:2027px">Our <span>Gallery</span></h2>
  <div class="photo" style="left:77px;top:2115px;width:406px;height:495px;background:linear-gradient(165deg,#5a6c82,#b8b4b0 55%,#e09a6a)" role="img" aria-label="Technician in hard hat splicing fibre cable on a rooftop"></div>
  <div class="photo" style="left:504px;top:2119px;width:296px;height:226px;background:linear-gradient(180deg,#5f8a3a,#3ab0b8 52%,#8a5a3a)" role="img" aria-label="Wooden deck beside a pool surrounded by tropical plants"></div>
  <div class="photo" style="left:820px;top:2119px;width:297px;height:226px;background:linear-gradient(180deg,#7ab0e0,#c8b8a0 60%,#7a9a5a)" role="img" aria-label="Paved city plaza with apartment towers"></div>
  <div class="photo" style="left:512px;top:2368px;width:602px;height:242px;background:linear-gradient(110deg,#3a4a3a,#6a8a3a 45%,#4a5a6a)" role="img" aria-label="Gardener laying drip irrigation line among shrubs"></div>
  <div class="btn btn-orange abs" style="left:535px;top:2647px;width:131px;height:43px;line-height:43px">View All</div>
</section>

<section class="contact">
  <h2 class="abs" style="left:0;width:1200px;text-align:center;top:50px;font-size:34px;font-weight:700;color:#fff">Contact Us</h2>
  <div class="field" style="left:145px;top:139px;width:448px;height:46px"><svg width="12" height="12" viewBox="0 0 12 12"><circle cx="6" cy="3.5" r="3" fill="#222"/><path d="M0 12a6 5 0 0 1 12 0z" fill="#222"/></svg>Name</div>
  <div class="field" style="left:613px;top:139px;width:452px;height:46px"><svg width="16" height="11" viewBox="0 0 16 11"><rect width="16" height="11" fill="#222"/><path d="M1 1l7 5 7-5" stroke="#fff" stroke-width="1.2" fill="none"/></svg>Email</div>
  <div class="field" style="left:145px;top:199px;width:448px;height:46px"><svg width="12" height="12" viewBox="0 0 24 24"><path d="M6.6 10.8a15 15 0 0 0 6.6 6.6l2.2-2.2a1 1 0 0 1 1-.25 11 11 0 0 0 3.6.6 1 1 0 0 1 1 1V20a1 1 0 0 1-1 1A17 17 0 0 1 3 4a1 1 0 0 1 1-1h3.5a1 1 0 0 1 1 1 11 11 0 0 0 .6 3.6 1 1 0 0 1-.25 1z" fill="#222"/></svg>Contact Number</div>
  <div class="field" style="left:613px;top:199px;width:452px;height:46px"><svg width="13" height="15" viewBox="0 0 13 15"><rect width="13" height="15" rx="1" fill="#222"/><path d="M3 4h7M3 7h7M3 10h7" stroke="#fff" stroke-width="1.2"/></svg>Subject</div>
  <div class="field" style="left:145px;top:259px;width:920px;height:165px;align-items:flex-start;padding-top:14px"><svg width="16" height="14" viewBox="0 0 16 14"><ellipse cx="8" cy="6" rx="8" ry="6" fill="#222"/><path d="M3 10l-1 4 5-3z" fill="#222"/><circle cx="5" cy="6" r="1" fill="#fff"/><circle cx="8" cy="6" r="1" fill="#fff"/><circle cx="11" cy="6" r="1" fill="#fff"/></svg>Your Messsage</div>
  <div class="btn btn-white abs" style="left:535px;top:440px;width:121px;height:44px;line-height:44px;color:#111">Submit</div>
</section>

<footer class="site-footer">
  <div class="abs" style="left:0;width:1200px;top:80px;text-align:center;color:var(--orange);font-weight:700;font-size:38px;line-height:42px;letter-spacing:1px">FENWICK<br><span style="font-size:26px;letter-spacing:3px;line-height:32px">GRADING LTD</span></div>
  <nav class="footer-nav"><span>Home</span><span>Irrigation installs</span><span>Service</span><span>Landscape Lighting</span><span>Fiber Optic Installation</span></nav>
  <div class="social"><span></span><span></span><span></span><span></span></div>
  <div class="footer-rule"></div>
  <p class="copyright">Copyright © 2024&nbsp; Fenwick Grading. All rights reserved.</p>
</footer>

</body>
</html>
```